Brivolt Technologies business card design

We need a business card designed with our new logo. it would be great if the card could communicate it is a technology based company.

Target Market(s)

system integrators

Industry/Entity Type

technology, IOT

Contact Information for Business Card

Name, designation, Address, telephone number, email address

Requirements
Must have
• logo and company name
Nice to have
• something to do with technology

```html
<!DOCTYPE html>
<html lang="en">
<head>
<meta charset="utf-8">
<title>Brivolt Technologies — Business Card</title>
<link href="https://fonts.googleapis.com/css2?family=Open+Sans:wght@400;600;700&display=swap" rel="stylesheet">
<style>
  :root {
    --backdrop: #3b3b3b;
    --paper: #ffffff;
    --ink: #3d3d3d;
    --ink-soft: #6a6a6a;
    --accent: #f28c1c;
    --card-dark: #111111;
    --white: #ffffff;
  }
  * { box-sizing: border-box; margin: 0; padding: 0; }
  html, body {
    width: 1200px; height: 801px; overflow: hidden;
    background: var(--backdrop);
    font-family: "Open Sans", Arial, sans-serif;
  }
  .stage {
    position: relative; width: 1200px; height: 801px;
    display: flex; align-items: center; justify-content: center; gap: 50px;
  }
  .card {
    position: relative; width: 525px; height: 300px;
    box-shadow: 0 18px 40px rgba(0,0,0,.45);
  }

  /* Front */
  .card--front {
    background: var(--paper);
    border-bottom: 3px solid var(--accent);
  }
  .brand {
    position: absolute; left: 36px; top: 112px;
    display: flex; align-items: center; gap: 12px;
  }
  .brand__square { width: 34px; height: 34px; background: var(--accent); }
  .brand__name {
    color: var(--ink); font-weight: 700; font-size: 26px; line-height: 1;
    letter-spacing: 1px; text-transform: uppercase;
  }
  .brand__name small { display: block; font-size: 13px; letter-spacing: 5px; margin-top: 5px; }

  .person {
    position: absolute; right: 34px; top: 34px; text-align: right;
  }
  .person__name { color: var(--accent); font-weight: 700; font-size: 19px; letter-spacing: .5px; }
  .person__title { color: var(--ink-soft); font-size: 13px; }
  .person__rule {
    position: absolute; right: 34px; top: 88px; width: 260px; height: 1px; background: var(--accent);
  }
  .address {
    position: absolute; right: 34px; top: 102px; text-align: right;
    color: var(--ink); font-size: 13px; line-height: 1.5;
  }

  .contact-rule {
    position: absolute; left: 36px; bottom: 94px; width: 230px; height: 1px; background: var(--accent);
  }
  .contact {
    position: absolute; left: 36px; bottom: 22px; list-style: none;
    color: var(--ink); font-size: 13px; line-height: 1.6;
  }
  .contact li { display: flex; align-items: center; gap: 8px; }
  .contact svg { width: 11px; height: 11px; fill: var(--accent); flex: none; }

  /* Back */
  .card--back {
    background: var(--card-dark);
    border-bottom: 2px solid var(--accent);
    overflow: hidden;
  }
  .back__mark-area {
    position: absolute; left: 0; top: 0; width: 290px; height: 100%;
    background: radial-gradient(circle at 55% 50%, #3a3a3a 0%, #1c1c1c 55%, var(--card-dark) 85%);
  }
  .back__brand {
    position: absolute; right: 34px; bottom: 58px; text-align: right;
    color: var(--white); font-weight: 700; text-transform: uppercase; line-height: 1;
  }
  .back__brand span { display: block; font-size: 38px; letter-spacing: 2px; }
  .back__brand small { display: block; font-size: 15px; letter-spacing: 7px; margin-top: 8px; }
</style>
</head>
<body>
<main class="stage">
  <article class="card card--front" aria-label="Business card front">
    <div class="brand">
      <span class="brand__square"></span>
      <p class="brand__name">Brivolt<small>Technologies</small></p>
    </div>

    <div class="person">
      <p class="person__name">DANIEL REYES</p>
      <p class="person__title">President</p>
    </div>
    <div class="person__rule"></div>
    <p class="address">3172 Marina Vista Way<br>Lakeport CA 95453</p>

    <div class="contact-rule"></div>
    <ul class="contact">
      <li><svg viewBox="0 0 24 24"><path d="M6.6 10.8a15 15 0 0 0 6.6 6.6l2.2-2.2a1 1 0 0 1 1-.25 11.4 11.4 0 0 0 3.6.57 1 1 0 0 1 1 1V20a1 1 0 0 1-1 1A17 17 0 0 1 3 4a1 1 0 0 1 1-1h3.5a1 1 0 0 1 1 1c0 1.25.2 2.45.57 3.57a1 1 0 0 1-.25 1z"/></svg>555-013-4872</li>
      <li><svg viewBox="0 0 24 24"><path d="M2 5h20v14H2zm2 2v.5l8 5 8-5V7l-8 5z"/></svg>info@brivolttech.com</li>
      <li><svg viewBox="0 0 24 24"><circle cx="12" cy="12" r="10"/></svg>www.brivolttech.com</li>
    </ul>
  </article>

  <article class="card card--back" aria-label="Business card back">
    <div class="back__mark-area" role="img" aria-label="Large faint brand symbol decoration"></div>
    <p class="back__brand"><span>Brivolt</span><small>Technologies</small></p>
  </article>
</main>
</body>
</html>
```